Business Card for Coastal Tundrabridge Advisory

We need a business card for Coastal Tundrabridge Advisory. The company website address is provided below. The company logo is attached. We provide specialized permafrost services to the mining, transportation, and oil & gas industries. The card should be prepared for:
Matthias Korhonen, PhD.
Coastal Tundrabridge Advisory
PO Box 418259
Quillwater, Alaska 99642
Direct: +1-907-555-0143
Email: mkorhonen@tundrabridgeadvisory.example
Website: www.coastaltundrabridgeadvisory.example

```html
<!DOCTYPE html>
<html lang="en">
<head>
<meta charset="utf-8">
<title>Coastal Tundrabridge Advisory — Business Card</title>
<link rel="stylesheet" href="https://fonts.googleapis.com/css2?family=Montserrat:wght@400;500;700&display=swap">
<style>
  :root {
    --backdrop: #1f1f1f;
    --card: #ffffff;
    --ink: #151a21;
    --ink-soft: #2b2f35;
  }
  * { margin: 0; padding: 0; box-sizing: border-box; }
  html, body {
    width: 1200px;
    height: 1059px;
    overflow: hidden;
    background: var(--backdrop);
    font-family: "Montserrat", sans-serif;
    color: var(--ink);
  }
  .card {
    position: absolute;
    background: var(--card);
    border-radius: 20px;
    overflow: hidden;
  }
  .card--front { left: 256px; top: 89px; width: 688px; height: 390px; }
  .card--back  { left: 252px; top: 546px; width: 696px; height: 395px; }

  .wordmark {
    font-weight: 700;
    text-transform: uppercase;
    color: var(--ink);
    white-space: nowrap;
  }
  .card--front .wordmark {
    position: absolute;
    left: 0; right: 0;
    top: 168px;
    text-align: center;
    font-size: 28px;
    letter-spacing: 1px;
  }
  .card--back .wordmark {
    position: absolute;
    left: 27px;
    top: 24px;
    font-size: 17px;
    letter-spacing: 0.5px;
  }

  .identity {
    position: absolute;
    right: 22px;
    top: 169px;
    text-align: right;
  }
  .identity__name { font-size: 21px; font-weight: 700; line-height: 1.3; }
  .identity__company { font-size: 18px; font-weight: 400; color: var(--ink-soft); line-height: 1.5; }
  .accent-bar {
    position: absolute;
    right: 0;
    top: 171px;
    width: 10px;
    height: 50px;
    background: var(--ink);
  }

  .address {
    position: absolute;
    left: 26px;
    top: 209px;
    font-size: 18px;
    line-height: 28px;
    color: var(--ink-soft);
  }
  .contacts {
    position: absolute;
    left: 27px;
    top: 294px;
    font-size: 18px;
    line-height: 27px;
    color: var(--ink-soft);
    list-style: none;
  }
  .contacts strong { font-weight: 700; color: var(--ink); }
</style>
</head>
<body>
  <section class="card card--front" aria-label="Card front">
    <p class="wordmark">Coastal Tundrabridge Advisory</p>
  </section>

  <section class="card card--back" aria-label="Card back">
    <p class="wordmark">Coastal Tundrabridge Advisory</p>

    <div class="identity">
      <p class="identity__name">Matthias Korhonen, PhD</p>
      <p class="identity__company">Coastal Tundrabridge Advisory</p>
    </div>
    <span class="accent-bar"></span>

    <address class="address" style="font-style:normal">
      PO Box 418259<br>
      Quillwater, Alaska 99642
    </address>

    <ul class="contacts">
      <li><strong>Direct:</strong> +1-907-555-0143</li>
      <li><strong>Email:</strong> mkorhonen@tundrabridgeadvisory.example</li>
      <li><strong>Website:</strong> www.coastaltundrabridgeadvisory.example</li>
    </ul>
  </section>
</body>
</html>
```